Little Dazzle Wren Flyer

Hi, Thank you for doing such a great job! I would like you to work with me on this flyer but give me a couple of option designs that I could choose from. To be honest im still a hundred per cent in what contents I want on this flyer but here it is. This is a double sided flyer!

One side is Little Dazzle Wren and the other side is Coastal Roving Face & Body.

I was thinking with Little Dazzle Wren I could have some slogan like Lets Party.... (something like that) I was thinking balloons etc. Also I have 4 boxes that I want to use with pictures with a little brief description in paragrapth order.

I don't have the description yet but will be writing it this weekend. I can upload later as I would like to get the design started. I would like you to use Spoil Us Soirees, Lovely in Lilac Tutu Party, Sir Groove Street Jam Party and lastly Garden Cups Buzzy Wren Party. You will see I have attached a photo of a ballet girl, hip hop photo, high tea photo and a pamper photo of two girls. These pictures are used in conjunction with each party theme. I will also need my number in large and including another number as well (I think) I will get back to that. as well as a email address ( I will also get back to you with that) my web address and a facebook thing to like.

Coastal Roving Face & Body

Basically this side is about our Adult Pamper Party. I would like to say something that I will forward to you. If wil only be breif, and a picture and promoting how the host received a free skin care kit of choice valued at $180 for hosting etc and maybe down the bottom of the page I could also in point form put my other services. I If you can start on Little Dazzle Wren that would be a good start and I can get back to you with more information on this one. This is a gift to me and they want me to pay for it now when I wasn't prepared with all my information for you. so please forgive me.

I was thinking this may be just for a A5 size but at some stage I will print both on a4 as well as poster size if this is possible.

You are probably confused as I am too. I will forward little dazzle wren pictures in order and then one for Coastal roving face and body (but I have another one coming on Monday) I will email you as necessary with more of my wording I need.

I know less is better so im trying not to put to much for Coastal roving but I think really like to talk a bit more about party options for little d w .

I will be going onto piclarder now to see if I can find another appro photo for pamper parties then apposed to one I sent. Im sure you will be not understanding my contents as im totally not prepared but I hope you can get started . And once again thank you very very much.

Target Market(s)

parents with children for little dazzle wren and women over the age of thirty for adult pamper parties on the opposite flyer

Industry/Entity Type

Adult

Requirements
Must have
• the last image of lady with mask on half her face . I would like that picture on Coastal rovng face and body side for pamper parties please. you can choose to ignore the girl with champagn glass if you wish as I need to put a picture of what thehost gets and I will upload that one within the next two days.
Should not have
• under the logo Coastal roving face and body I want the words healthier looking skin taken out please

```html
<!DOCTYPE html>
<html lang="en">
<head>
<meta charset="utf-8">
<title>Coastal Roving Face &amp; Body – Adult Pamper Party Flyer</title>
<link rel="stylesheet" href="https://fonts.googleapis.com/css2?family=EB+Garamond:wght@400;500&display=swap">
<style>
  :root {
    --canvas-bg: #ece9ea;
    --paper: #ffffff;
    --brand-pink: #d62a80;
    --ink-grey: #5a5556;
    --ink-soft: #6e6869;
    --photo-dark: #2a1d18;
    --photo-skin: #c99a7a;
    --photo-light: #efe6e0;
  }
  * { box-sizing: border-box; margin: 0; padding: 0; }
  html, body {
    width: 1200px; height: 1000px; overflow: hidden;
    background: var(--canvas-bg);
    font-family: "EB Garamond", Georgia, serif;
  }
  .flyer {
    position: absolute; left: 350px; top: 30px;
    width: 500px; height: 940px;
    background: var(--paper);
    box-shadow: 0 4px 18px rgba(0,0,0,.12);
    overflow: hidden;
  }
  .flyer-edge {
    position: absolute; right: 10px; top: 0; bottom: 0;
    border-right: 2px dotted var(--brand-pink);
  }
  .flyer-title {
    position: absolute; left: 28px; top: 34px;
    font-size: 44px; font-weight: 400; color: var(--brand-pink);
    letter-spacing: .5px; white-space: nowrap;
  }
  .brand {
    position: absolute; left: 318px; top: 104px; width: 160px;
    color: var(--brand-pink); line-height: 1.25;
  }
  .brand-square {
    width: 56px; height: 56px; background: var(--brand-pink); margin-bottom: 6px;
  }
  .brand-name { font-size: 12px; white-space: nowrap; }
  .brand-contact {
    margin-top: 4px; padding-top: 4px;
    border-top: 1px solid var(--brand-pink);
    color: var(--ink-grey);
  }
  .brand-phone { font-size: 17px; color: var(--brand-pink); }
  .brand-email { font-size: 11px; white-space: nowrap; }
  .hero-photo {
    position: absolute; left: 0; top: 160px;
    width: 300px; height: 600px;
    background: linear-gradient(160deg, var(--photo-dark) 0%, var(--photo-light) 30%, var(--photo-skin) 62%, var(--photo-light) 100%);
  }
  .host-offer {
    position: absolute; left: 318px; top: 290px; width: 165px;
    font-size: 27px; line-height: 1.7; color: var(--ink-grey);
    white-space: nowrap;
  }
  .tagline {
    position: absolute; right: 24px; top: 700px;
    font-size: 20px; color: var(--brand-pink); white-space: nowrap;
  }
  .services {
    position: absolute; left: 28px; top: 784px; width: 440px;
    font-size: 17px; line-height: 1.75; color: var(--ink-soft);
  }
</style>
</head>
<body>
  <main class="flyer">
    <div class="flyer-edge"></div>

    <h1 class="flyer-title">Adult Pamper Party</h1>

    <div class="brand">
      <div class="brand-square"></div>
      <div class="brand-name">Coastal Roving Face &amp; Body</div>
      <div class="brand-contact">
        <div class="brand-phone">0400 318 627</div>
        <div class="brand-email">hello@coastalroving.com.au</div>
      </div>
    </div>

    <div class="hero-photo" role="img" aria-label="Photo of a relaxed woman with a towel on her head receiving a cream face mask applied with a brush"></div>

    <p class="host-offer">Host will<br>receive a free<br>skin care kit<br>of choice<br>valued at<br>$180 !</p>

    <p class="tagline">Love your skin</p>

    <p class="services">
      Coastal Roving Face &amp; Body also offers:<br>
      Facials &amp; Peels, Microdermabrasion, 10 min. Liquid Facelifting,<br>
      Oxygen Infusion, Derma Rolling &amp; Skin Needling,<br>
      Tinting &amp; Waxing, Skin Care Products
    </p>
  </main>
</body>
</html>
```